Contemporary Business card for Event Manager

Needed for my startup events company in Melbourne. Events I manage will be based within the fashion industry, sporting events, product launches etc. Not weddings or small dinner parties. Therfore I am after something professional and aimed at high end corporate market; but with the added emphasis on not being too conservative or boring. I am happy with a pop of colour e.g. yellow or copper foil.

Target Market(s)

fashion industry, design industry, high end sporting events e.g. Polo, Grand Prix, corporate clients,

Industry/Entity Type

Fashion

Contact Information for Business Card

side 1
Lucy Brandt (can be upper or lower case, have a feature full stop between first and surname, or at the end of the nameetc) I am open to ideas. I would also be fine with my initials or name as a logo on the front (if this is the case my full name would need to go on the second side of the card.
2nd side:
Mobile: +61 400 817 263
email: lucy.brandt@mailnest.com.au

on one side of the card:
event management | brand activation | Advisory Services

Font styles to use
Serif
Sans Serif

Requirements
Must have
• side 2 must have
• mobile number
• email address
• event management | brand activation | Advisory Services
• ** my full name (Lucy Brandt) must be on the card somewhere)
Nice to have
• 1st side
• I see the card stock being either a dark grey, light grey, natural white or black (all matt colours on unprocessed card). I see the writing being copper foil, or foil white or foil black.
• To give you a feel for me, think: contemporary, minimalist, I love line drawings, concrete, white with grey vein marble, copper, white, grey, black...yes I do like colour....yellow (but pops of colour) ;) I would like the card to look designer but 'on trend' as I deal with a lot of design and fashion clients....styles - think the sophistication and simplicity of Vireaux or urban contemporary.
• some examples of what I like. Although please don't leet this limit you...I really am happy to have something a little more urban or design focused like a line drawing of an object, person too or a photo image too.
• https://www.moodtackle.com/pin/830165427719302846/
• https://www.moodtackle.com/pin/607281935540173268/
• https://www.moodtackle.com/pin/318746205913457092/
• https://www.moodtackle.com/pin/41983627530918476/
• https://www.moodtackle.com/pin/53128940672419087/
• https://www.moodtackle.com/pin/90316284750638152/
• https://www.moodtackle.com/pin/734092618450362918/
• https://www.moodtackle.com/pin/926354081736215407/
• https://www.moodtackle.com/pin/481627093518704356/
Should not have
• should not look commercial or have cartoonish looking logos. However happy with a simple line drawing or logo with initials etc.

```html
<!DOCTYPE html>
<html lang="en">
<head>
<meta charset="utf-8">
<title>Lucy Brandt — Business Card</title>
<link rel="stylesheet" href="https://fonts.googleapis.com/css2?family=Tinos:wght@400&display=swap">
<style>
  :root {
    --backdrop: #e4e2df;
    --card-black: #111112;
    --card-charcoal: #2a2a2c;
    --band-grey: #4a4a4c;
    --foil-white: #f2f2f2;
    --stock-white: #f7f7f6;
    --ink: #141414;
    --rule: #9a9a9a;
    --mid-grey: #8c8c8c;
    --light-grey: #c4c4c4;
  }
  * { margin: 0; padding: 0; box-sizing: border-box; }
  html, body {
    width: 1200px; height: 902px; overflow: hidden;
    background: var(--backdrop);
    font-family: "Tinos", "Times New Roman", serif;
  }
  .sheet {
    position: relative; width: 1200px; height: 902px;
    display: flex; align-items: center; justify-content: center; gap: 40px;
  }
  .card {
    position: relative; width: 540px; height: 309px; overflow: hidden;
    box-shadow: 0 8px 22px rgba(0,0,0,0.22);
  }
  .card svg { position: absolute; inset: 0; width: 100%; height: 100%; }
  .card-front { background: var(--card-black); }
  .card-front .name {
    position: absolute; left: 262px; top: 103px;
    color: var(--foil-white); font-size: 34px; letter-spacing: 0.5px; line-height: 1;
  }
  .card-back { background: var(--stock-white); }
  .card-back .phone {
    position: absolute; left: 72px; top: 118px;
    font-size: 31px; color: var(--ink); line-height: 1;
  }
  .card-back .email {
    position: absolute; right: 34px; top: 100px;
    font-size: 12.5px; color: var(--ink);
  }
  .card-back .services {
    position: absolute; right: 34px; top: 128px;
    list-style: none; text-align: right; font-size: 13.5px; line-height: 1.05; color: var(--ink);
  }
</style>
</head>
<body>
<main class="sheet">
  <section class="card card-front" aria-label="Card front">
    <svg viewBox="0 0 540 309" aria-hidden="true">
      <defs>
        <linearGradient id="lower-panel" x1="0" y1="0" x2="1" y2="1">
          <stop offset="0" stop-color="#3a3a3c"/>
          <stop offset="1" stop-color="#1c1c1e"/>
        </linearGradient>
      </defs>
      <path d="M0 214 L300 205 Q360 262 420 309 L0 309 Z" fill="url(#lower-panel)"/>
      <rect x="255" y="96" width="285" height="46" fill="var(--band-grey)"/>
      <path d="M236 0 Q205 170 420 309" fill="none" stroke="var(--foil-white)" stroke-width="4"/>
      <line x1="0" y1="212" x2="292" y2="203" stroke="var(--foil-white)" stroke-width="4"/>
    </svg>
    <div class="name">Lucy.Brandt</div>
  </section>

  <section class="card card-back" aria-label="Card back">
    <svg viewBox="0 0 540 309" aria-hidden="true">
      <defs>
        <linearGradient id="grey-band" x1="0" y1="0" x2="1" y2="0">
          <stop offset="0" stop-color="var(--mid-grey)"/>
          <stop offset="0.5" stop-color="var(--light-grey)"/>
          <stop offset="0.75" stop-color="#9a9a9a"/>
          <stop offset="1" stop-color="#6e6e6e"/>
        </linearGradient>
      </defs>
      <line x1="0" y1="64" x2="540" y2="64" stroke="var(--rule)" stroke-width="1"/>
      <rect x="40" y="124" width="24" height="24" fill="var(--card-charcoal)"/>
      <rect x="390" y="178" width="150" height="46" fill="var(--card-black)"/>
      <polygon points="300,224 390,224 390,178" fill="#555"/>
      <rect x="110" y="224" width="430" height="46" fill="url(#grey-band)"/>
    </svg>
    <div class="phone">61 400 817 263</div>
    <div class="email">lucy.brandt@mailnest.com.au</div>
    <ul class="services">
      <li>event management</li>
      <li>brand activation</li>
      <li>Advisory Services</li>
    </ul>
  </section>
</main>
</body>
</html>
```